Distribution/Printing company needs a web site to inform prospective customers on what we do.

Distribution/Printing/Packaging company needs a web site to inform prospective customers on what we do. Please look at our direct to consumer web site (under development) for an idea of the product lines we sell: storedev.maplewickhaven.com
Logo files are attached as is a flyer that is under development which contains other information about the company (this is to be used for content- not to be posted as is). The web site should be focused on our business customer base and is not intended to be direct to consumer. Site should have a link to our consumer web site.
Site design should be mobile friendly, or mobile could be redirected to a mobile version. This web site will be strictly informational and will not be designed for any sales transactions.

Target Market(s)

Manufacturing and retail businesses, any other multi-site business that would benefit from centralized pricing and budget controls we can provide (banks, medical/dental offices, educational facilities, etc).

Industry/Entity Type

It Company

Coding

Coded - Design and coding required

Number of Pages Required

5+ page

Requirements
Must have
• 1) Top level menu: Products, about us, locations, contact us, news
• 2) page with news/promotions that is easily updated
• 3) "contact us" form (name, company, phone, email address) email link
• 4) link to www.store.maplewickhaven.com with information that lower pricing is available for businesses
• 5) SEO keywords
• 6) Link to powerpoint presentation file
Nice to have
• 1) our phone number should appear on every page near the top

```html
<!DOCTYPE html>
<html lang="en">
<head>
<meta charset="utf-8">
<title>Maplewick Haven Supply</title>
<link href="https://fonts.googleapis.com/css2?family=Open+Sans:wght@400;600;700&display=swap" rel="stylesheet">
<style>
:root{
  --band:#e4e4e4;
  --nav:#3a3a3a;
  --ink:#333333;
  --muted:#777777;
  --line:#dddddd;
  --gold:#c9962a;
  --footer:#3b3b3b;
  --footer-dark:#2b2b2b;
  --footer-text:#e6e6e6;
  --red:#d8201c;
  --social:#2a6fb8;
}
*{box-sizing:border-box;margin:0;padding:0}
html,body{width:798px;height:1200px;overflow:hidden;background:#fff;font-family:"Open Sans",Arial,sans-serif;color:var(--ink)}
.page{position:relative;width:798px;height:1200px;overflow:hidden}
.abs{position:absolute}
.top-band{left:0;top:0;width:798px;height:330px;background:var(--band)}
.brand{left:114px;top:34px;display:flex;align-items:flex-start;gap:7px}
.brand-mark{display:block;width:12px;height:12px;background:var(--ink);margin-top:2px}
.brand-name{font-size:10.5px;font-weight:700;letter-spacing:.2px;color:#222;white-space:nowrap}
.brand-tag{font-size:7px;font-weight:600;color:#222;margin-top:2px;white-space:nowrap}
.search{left:526px;top:37px;width:158px;height:24px;border:1px solid #ccc;background:#fff;display:flex}
.search span{flex:1;font-size:7px;color:#666;padding:7px 8px}
.search b{width:27px;background:#2f2f2f;display:flex;align-items:center;justify-content:center}
.nav{left:114px;top:96px;width:570px;height:37px;background:var(--nav);display:flex;align-items:center;padding-left:15px}
.nav a{color:#fff;text-decoration:none;font-size:9.5px;white-space:nowrap;padding-right:12px;margin-right:12px;border-right:1px solid #ddd;line-height:11px}
.nav a:last-child{border:none;margin-right:0;padding-right:0}
.hero{left:114px;top:133px;width:570px;height:251px;background:linear-gradient(90deg,#f4f4f4,#e9e7e4 60%,#ecebe9);box-shadow:0 6px 8px -6px rgba(0,0,0,.35)}
.hero-photo{left:20px;top:40px;width:280px;height:190px;background:linear-gradient(135deg,#d9c7ae,#b08a63);border-radius:4px;opacity:.85}
.hero-title{left:226px;top:74px;width:300px;text-align:right;font-size:17px;font-weight:600;color:#444;white-space:nowrap;line-height:22px}
.hero-rule{left:291px;top:110px;width:235px;height:1px;background:#555}
.hero-rule i{position:absolute;right:0;top:-1px;width:75px;height:2px;background:var(--gold)}
.hero-text{left:300px;top:130px;width:226px;text-align:right;font-size:9px;line-height:15px;color:#444}
.dots{left:494px;top:179px;display:flex;gap:3px}
.dots i{width:7px;height:7px;border-radius:50%;background:#777;border:1px solid #555}
.dots i.on{background:#222}
.card{width:183px;height:134px;border:1px solid var(--line);top:417px;background:#fff}
.card-photo{height:105px}
.card p{text-align:center;font-size:10px;color:#444;padding-top:8px}
.intro{left:114px;top:566px;width:475px;font-size:7.2px;line-height:13px;color:#555}
.btn{left:610px;top:570px;width:74px;height:24px;background:#3a3a3a;color:#fff;font-size:8.5px;font-weight:600;display:flex;align-items:center;justify-content:center;border-radius:2px}
.divider{left:0;top:638px;width:798px;height:1px;background:#eee}
.section-title{font-size:15px;font-weight:400;color:#333;white-space:nowrap}
.arrow{width:13px;height:13px;top:662px}
.offer{top:698px;width:136px;height:130px;border:1px solid #d6d6d6;background:#fff}
.offer-photo{position:absolute;left:14px;top:6px;width:108px;height:92px;border-radius:4px}
.offer-rule{position:absolute;left:14px;top:101px;width:108px;height:1px;background:#eee}
.offer p{position:absolute;left:0;right:0;top:109px;text-align:center;font-size:10px;color:#333}
.news{top:904px;width:176px;height:49px;background:#efefef;display:flex}
.news-date{width:34px;background:var(--gold);color:#8a5f10;text-align:center;font-weight:700;padding-top:11px}
.news-date small{display:block;font-size:8px;line-height:9px}
.news-date strong{display:block;font-size:14px;line-height:15px}
.news-body{padding:9px 0 0 13px}
.news-body h3{font-size:7.6px;font-weight:400;color:#222;margin-bottom:4px;white-space:nowrap}
.news-body p{font-size:6px;line-height:9px;color:#888;width:120px}
.footer{left:0;top:986px;width:798px;height:174px;background:var(--footer)}
.fcol{top:1014px;color:var(--footer-text)}
.fcol h4{font-size:9px;font-weight:400;margin-bottom:11px;white-space:nowrap}
.fcol li{list-style:none;font-size:7px;line-height:13.5px;padding-left:11px;position:relative;white-space:nowrap}
.fcol li:before{content:"";position:absolute;left:0;top:5px;border-left:3px solid #ddd;border-top:2px solid transparent;border-bottom:2px solid transparent}
.fsep{top:986px;width:1px;height:174px;background:#353535}
.news-sign p{font-size:7px;line-height:10px;color:#ccc;width:140px;margin-bottom:8px}
.field{width:135px;height:19px;background:#efefef;border:1px solid #fff;font-size:6px;color:#444;padding:5px 7px;margin-bottom:9px}
.subscribe{width:51px;height:16px;background:var(--red);color:#fff;font-size:6px;font-weight:700;display:flex;align-items:center;justify-content:center;border-radius:2px;box-shadow:0 1px 2px rgba(0,0,0,.5)}
.bottom{left:0;top:1160px;width:798px;height:40px;background:var(--footer-dark)}
.copy{left:114px;top:1177px;font-size:6.5px;color:#999;white-space:nowrap}
.social{top:1171px;display:flex;gap:5px;left:575px}
.social i{width:16px;height:16px;background:var(--social);display:block}
</style>
</head>
<body>
<div class="page">
  <div class="abs top-band"></div>

  <div class="abs brand">
    <span class="brand-mark"></span>
    <div>
      <div class="brand-name">MAPLEWICK HAVEN SUPPLY</div>
      <div class="brand-tag">Packaging • Printing • Distribution</div>
    </div>
  </div>

  <div class="abs search">
    <span>Search</span>
    <b><svg width="11" height="11" viewBox="0 0 11 11"><circle cx="4.5" cy="4.5" r="3.3" fill="none" stroke="#fff" stroke-width="1.3"/><line x1="7" y1="7" x2="10.3" y2="10.3" stroke="#fff" stroke-width="1.5"/></svg></b>
  </div>

  <nav class="abs nav">
    <a>Home</a><a>About Us</a><a>Category</a><a>Destribution</a><a>Printing</a><a>Packaging</a><a>News</a><a>Contact Us</a>
  </nav>

  <section class="abs hero">
    <div class="abs hero-photo" role="img" aria-label="Warehouse worker leaning on a stack of cardboard boxes"></div>
    <h1 class="abs hero-title">Maplewick Haven Supply</h1>
    <div class="abs hero-rule"><i></i></div>
    <p class="abs hero-text">Quasi architecto beatae vitae dicta sunt&nbsp; enim voluptatem quia voluptas sit aspernatur consequuntur magni dolores</p>
    <div class="abs dots"><i></i><i class="on"></i><i></i></div>
  </section>

  <div class="abs card" style="left:114px"><div class="card-photo" role="img" aria-label="Courier delivering a parcel to a customer" style="background:linear-gradient(135deg,#c9a98a,#e2c7a4 60%,#a3876a)"></div><p>Distribution</p></div>
  <div class="abs card" style="left:307px"><div class="card-photo" role="img" aria-label="Worker taping boxes in a warehouse" style="background:linear-gradient(135deg,#b48a6c,#c7ad94 50%,#6b7fa6)"></div><p>Printing</p></div>
  <div class="abs card" style="left:501px"><div class="card-photo" role="img" aria-label="Brown paper wrapped parcels with tags" style="background:linear-gradient(135deg,#8a6140,#b88a5c 55%,#7a5638)"></div><p>Packaging</p></div>

  <p class="abs intro">Sed ut perspiciatis unde omnis iste natus error sit voluptatem accusantium doloremque laudantium, totam rem aperiam, eaque ipsa quae ab illo inventore veritatis et quasi architecto beatae vitae dicta sunt explicabo. Nemo enim ipsam voluptatem quia voluptas sit aspernatur&nbsp;&nbsp; aut odit aut fugit, sed quia consequuntur</p>
  <div class="abs btn">Read More</div>

  <div class="abs divider"></div>

  <h2 class="abs section-title" style="left:115px;top:657px">What we offer</h2>
  <svg class="abs arrow" style="left:651px" viewBox="0 0 13 13"><circle cx="6.5" cy="6.5" r="5.8" fill="#fff" stroke="#333" stroke-width="1"/><path d="M7.8 3.8 4.6 6.5 7.8 9.2Z" fill="#333"/></svg>
  <svg class="abs arrow" style="left:670px" viewBox="0 0 13 13"><circle cx="6.5" cy="6.5" r="5.8" fill="#fff" stroke="#333" stroke-width="1"/><path d="M5.2 3.8 8.4 6.5 5.2 9.2Z" fill="#333"/></svg>

  <div class="abs offer" style="left:114px"><div class="offer-photo" role="img" aria-label="Open cardboard boxes" style="background:radial-gradient(circle,#d6aa66 0,#e8d1a8 45%,#fff 75%)"></div><div class="offer-rule"></div><p>Packages</p></div>
  <div class="abs offer" style="left:259px"><div class="offer-photo" role="img" aria-label="Calculator, stapler and office stationery" style="background:radial-gradient(circle,#555 0,#9a8f8f 40%,#fff 75%)"></div><div class="offer-rule"></div><p>Office</p></div>
  <div class="abs offer" style="left:404px"><div class="offer-photo" role="img" aria-label="Coloured plastic storage bins" style="background:radial-gradient(circle,#d9c43a 0,#7a8fcf 40%,#fff 75%)"></div><div class="offer-rule"></div><p>Storage</p></div>
  <div class="abs offer" style="left:548px"><div class="offer-photo" role="img" aria-label="Roadside emergency and industrial safety kit" style="background:radial-gradient(circle,#d33 0,#e58a6a 40%,#fff 75%)"></div><div class="offer-rule"></div><p>Industrial</p></div>

  <h2 class="abs section-title" style="left:114px;top:859px">Latest News</h2>

  <article class="abs news" style="left:114px"><div class="news-date"><small>MAY</small><strong>25</strong></div><div class="news-body"><h3>Architecto beatae vitae dicta</h3><p>magni dolores eos qui ratione sequi nesciunt. Neque porro</p></div></article>
  <article class="abs news" style="left:311px"><div class="news-date"><small>APRIL</small><strong>25</strong></div><div class="news-body"><h3>Architecto beatae vitae dicta</h3><p>magni dolores eos qui ratione sequi nesciunt. Neque porro</p></div></article>
  <article class="abs news" style="left:508px"><div class="news-date"><small>MAY</small><strong>25</strong></div><div class="news-body"><h3>Architecto beatae vitae dicta</h3><p>magni dolores eos qui ratione sequi nesciunt. Neque porro</p></div></article>

  <footer class="abs footer"></footer>
  <div class="abs fsep" style="left:202px"></div>
  <div class="abs fsep" style="left:331px"></div>
  <div class="abs fsep" style="left:497px"></div>

  <div class="abs fcol" style="left:120px"><h4>QUICK LINKS</h4><ul><li>About Uss</li><li>Category</li><li>Distribution</li><li>Printing</li><li>Packages</li><li>News</li><li>Contact Us</li></ul></div>
  <div class="abs fcol" style="left:225px;top:1016px"><h4>OTHER LINKS</h4><ul><li>Packaging</li><li>Office Supplies</li><li>Janitorial</li><li>Retail Supplies</li></ul></div>
  <div class="abs fcol" style="left:356px;top:1016px"><h4>SUPPORT</h4><ul><li>Packaging</li><li>Office Supplies</li><li>Storage</li><li>Industial</li><li>Retails</li></ul></div>
  <div class="abs fcol news-sign" style="left:526px;top:1016px">
    <h4 style="margin-left:3px">NEWSLETTER SIGN UP</h4>
    <p>Sign up for our daily email by entering your information below</p>
    <div class="field">Name:</div>
    <div class="field">Email Address:</div>
    <div class="subscribe">SUBSCRIBE</div>
  </div>

  <div class="abs bottom"></div>
  <div class="abs copy">Copyrights @ 2015 Maplewick Haven All Rights Reserved.</div>
  <div class="abs social" aria-label="Social links"><i></i><i></i><i></i><i></i></div>
</div>
</body>
</html>
```